Using attached logo that has been created

Business card with logo that's attached. Maybe with water or the cartoon van in background. Looking for it to not be so plain and not too white.
Information to include;
Rodney Ashcombe
(555) 218-7730
Info@bramleypipeworks.example
www.bramleypipeworks.example
License # 4627195
Looking forward to the designs u come up with.
Thank you!
-Delphine
Target Market(s)
Plumbing
Industry/Entity Type
Plumbing
Contact Information for Business Card
Listed above

```html
<!DOCTYPE html>
<html lang="en">
<head>
<meta charset="utf-8">
<title>Bramley Pipeworks – Business Card</title>
<link href="https://fonts.googleapis.com/css2?family=Raleway:wght@500;700&display=swap" rel="stylesheet">
<style>
  :root {
    --stage: #2b2b2b;
    --brand-blue: #0f55a8;
    --brand-yellow: #fdc010;
    --name-yellow: #f6c21a;
    --white: #ffffff;
    --van-tone: #e4e8ec;
    --figure-tone: #5f7fb3;
    --water-deep: #2f4d73;
    --water-light: #a9c3d8;
  }
  html, body {
    margin: 0;
    width: 1075px;
    height: 1200px;
    overflow: hidden;
    background: var(--stage);
    font-family: "Raleway", sans-serif;
  }
  .card {
    position: absolute;
    left: 206px;
    width: 663px;
    height: 395px;
    overflow: hidden;
    box-shadow: 3px 3px 0 rgba(0,0,0,0.55);
  }
  .card--front { top: 187px; background: var(--brand-blue); }
  .card--back { top: 637px; }
  .card__split { position: absolute; inset: 0; }
  .contact__name {
    position: absolute;
    left: 29px;
    top: 46px;
    margin: 0;
    font-size: 25px;
    font-weight: 700;
    color: var(--name-yellow);
    letter-spacing: 0.2px;
  }
  .contact__list {
    position: absolute;
    left: 26px;
    top: 104px;
    margin: 0;
    padding: 0;
    list-style: none;
  }
  .contact__item {
    display: flex;
    align-items: center;
    gap: 6px;
    height: 23.5px;
    font-size: 18.5px;
    font-weight: 500;
    color: var(--white);
  }
  .contact__icon { width: 18px; height: 18px; flex: none; }
  .art { position: absolute; }
  .art--van {
    left: 0; top: 195px; width: 430px; height: 200px;
    background: linear-gradient(180deg, var(--van-tone), #c9d0d8);
    border-radius: 40px 90px 0 0;
  }
  .art--figure-front {
    left: 478px; top: 42px; width: 124px; height: 158px;
    background: linear-gradient(180deg, #8a6d55 0%, var(--figure-tone) 50%, #9a8a6a 100%);
    border-radius: 50px 50px 12px 12px;
    opacity: 0.9;
  }
  .brand {
    position: absolute;
    display: flex;
    align-items: center;
    justify-content: center;
    gap: 7px;
    font-weight: 700;
    color: var(--brand-blue);
    white-space: nowrap;
  }
  .brand__mark { width: 11px; height: 11px; flex: none; background: currentColor; border-radius: 50%; }
  .brand--front { left: 400px; top: 212px; width: 244px; font-size: 21px; }
  .license {
    position: absolute;
    left: 450px;
    top: 348px;
    font-size: 17px;
    font-weight: 500;
    color: var(--brand-blue);
  }
  .art--water {
    inset: 0;
    background: radial-gradient(ellipse at 85% 80%, var(--water-light) 0%, #6e8fb0 45%, var(--water-deep) 100%);
  }
  .art--figure-back {
    left: 275px; top: 32px; width: 166px; height: 210px;
    background: linear-gradient(180deg, #8a6d55 0%, var(--figure-tone) 50%, #9a8a6a 100%);
    border-radius: 66px 66px 14px 14px;
    opacity: 0.9;
  }
  .brand--back { left: 166px; top: 256px; width: 336px; font-size: 29px; color: var(--white); }
  .brand--back .brand__mark { width: 14px; height: 14px; }
</style>
</head>
<body>
  <section class="card card--front" aria-label="Business card front">
    <svg class="card__split" viewBox="0 0 663 395" aria-hidden="true">
      <polygon points="444,0 663,0 663,395 204,395" fill="var(--brand-yellow)"/>
    </svg>
    <h1 class="contact__name">RODNEY ASHCOMBE</h1>
    <ul class="contact__list">
      <li class="contact__item">
        <svg class="contact__icon" viewBox="0 0 24 24"><path d="M6.6 10.8a15 15 0 0 0 6.6 6.6l2.2-2.2a1 1 0 0 1 1-.25 11.4 11.4 0 0 0 3.6.57 1 1 0 0 1 1 1V20a1 1 0 0 1-1 1A17 17 0 0 1 3 4a1 1 0 0 1 1-1h3.5a1 1 0 0 1 1 1c0 1.25.2 2.450.57 3.57a1 1 0 0 1-.25 1z" fill="var(--brand-yellow)"/></svg>
        (555) 218-7730
      </li>
      <li class="contact__item">
        <svg class="contact__icon" viewBox="0 0 24 24"><rect x="2" y="5" width="20" height="14" fill="var(--brand-yellow)"/><path d="M2 5l10 8 10-8" fill="none" stroke="var(--brand-blue)" stroke-width="1.6"/></svg>
        Info@bramleypipeworks.example
      </li>
      <li class="contact__item">
        <svg class="contact__icon" viewBox="0 0 24 24"><circle cx="12" cy="12" r="9.5" fill="var(--brand-yellow)"/><g fill="none" stroke="var(--brand-blue)" stroke-width="1.3"><ellipse cx="12" cy="12" rx="4" ry="9.5"/><path d="M2.5 12h19M4 7h16M4 17h16"/></g></svg>
        www.bramleypipeworks.example
      </li>
    </ul>
    <div class="art art--van" role="img" aria-label="Cartoon white work van with a smiling plumber holding a wrench out of the driver window"></div>
    <div class="art art--figure-front" role="img" aria-label="Cartoon bearded plumber in a blue shirt holding a pipe wrench and a circular saw"></div>
    <div class="brand brand--front"><span class="brand__mark"></span>Bramley Pipeworks</div>
    <div class="license">License # 4627195</div>
  </section>

  <section class="card card--back" aria-label="Business card back">
    <div class="art art--water" role="img" aria-label="Water droplets on a blue glass surface"></div>
    <div class="art art--figure-back" role="img" aria-label="Cartoon bearded plumber in a blue shirt holding a pipe wrench and a circular saw"></div>
    <div class="brand brand--back"><span class="brand__mark"></span>Bramley Pipeworks</div>
  </section>
</body>
</html>
```